Hartwell Estates Business Cards

I would like a business card that includes myself and my partner.
Includes: Logo, office #, email, website, our names, our numbers and possibly the address. I would also like the logo to be embossed and the card to be horizontal.
There is a photo of our yard signs to give you an idea of the colors of our business.

Target Market(s)

Everyone in real estate market.
We are in a rural area. Our clientele are from all socioeconomic backgrounds.

Industry/Entity Type

Real Estate Agent

Contact Information for Business Card

Company Name: Hartwell Estates
Our Names, Titles & Cell #'s : Dana Pembrook-Broker (555).317.6624, Marla Pembrook-Realtor (555).609.1385
Office #: (555).240.3918
Website: hartwellestates-demo.com
Joint Email: pembrook@hartwellestates-demo.com
Office Address: 418B W. Calloway Ave.
Fernvale, KS. 70913

Font styles to use
Serif

Requirements
Must have
• HORIZONTAL, Logo, Myself and my partners names, Our cell #'s, our office #, our website, our email address
Nice to have
• Embossed logo, office address, our titles.

```html
<!DOCTYPE html>
<html lang="en">
<head>
<meta charset="utf-8">
<title>Hartwell Estates Business Cards</title>
<link href="https://fonts.googleapis.com/css2?family=Montserrat:wght@400;500;600&display=swap" rel="stylesheet">
<style>
  :root {
    --backdrop: #2b2b2d;
    --olive: #6b6548;
    --olive-deep: #5e583d;
    --purple: #4a1372;
    --white: #ffffff;
    --ink-soft: #6b6548;
  }
  * { box-sizing: border-box; margin: 0; padding: 0; }
  html, body { width: 1200px; height: 900px; overflow: hidden; }
  body {
    background: var(--backdrop);
    font-family: "Montserrat", Arial, sans-serif;
    position: relative;
  }
  .card {
    position: absolute;
    left: 250px;
    width: 700px;
    height: 400px;
    border-radius: 20px;
    overflow: hidden;
  }
  .card svg.bands { position: absolute; inset: 0; }

  /* Back */
  .card--back { top: 40px; background: var(--olive); }
  .back-mark {
    position: absolute;
    top: 130px; left: 0; width: 100%;
    text-align: center;
    font-size: 54px;
    font-weight: 500;
    color: var(--olive-deep);
    letter-spacing: 1px;
  }
  .back-web {
    position: absolute;
    right: 40px; top: 280px;
    color: var(--white);
    font-size: 19px;
    letter-spacing: 0.3px;
  }
  .back-web strong { font-weight: 600; }

  /* Front */
  .card--front { top: 470px; background: var(--white); }
  .brand {
    position: absolute;
    left: 40px; top: 100px;
    display: flex; align-items: center; gap: 12px;
    color: var(--purple);
    font-size: 26px; font-weight: 600;
    letter-spacing: 0.5px;
  }
  .brand-square { width: 22px; height: 22px; background: var(--purple); }
  .divider {
    position: absolute;
    left: 40px; right: 40px; top: 228px;
    height: 2px; background: var(--purple);
  }
  .agent { position: absolute; right: 40px; text-align: right; }
  .agent-name { color: var(--purple); font-size: 23px; font-weight: 600; line-height: 1.1; }
  .agent-title { color: var(--ink-soft); font-size: 13px; }
  .agent-phone { color: var(--purple); font-size: 15px; }
  .agent--broker { top: 150px; }
  .agent--realtor { top: 238px; }
  .office {
    position: absolute;
    left: 40px; top: 240px;
    color: var(--purple);
    font-size: 15px;
    line-height: 1.35;
  }
  .office-list { list-style: none; margin-top: 6px; }
  .office-list li { display: flex; align-items: center; gap: 10px; }
  .office-list svg { width: 11px; height: 11px; flex: none; }
  .office-list .web strong { font-weight: 600; }
</style>
</head>
<body>

<section class="card card--back" aria-label="Card back">
  <svg class="bands" viewBox="0 0 700 400" aria-hidden="true">
    <polygon points="0,352 525,334 500,400 0,400" fill="var(--purple)"/>
    <polygon points="525,334 700,318 700,332 512,368" fill="var(--white)"/>
  </svg>
  <div class="back-mark">Hartwell Estates</div>
  <div class="back-web">www.<strong>hartwellestates-demo</strong>.com</div>
</section>

<section class="card card--front" aria-label="Card front">
  <svg class="bands" viewBox="0 0 700 400" aria-hidden="true">
    <polygon points="0,382 470,366 462,400 0,400" fill="var(--olive)"/>
    <polygon points="500,330 700,310 700,400 478,400" fill="var(--purple)"/>
  </svg>

  <div class="brand"><span class="brand-square"></span>Hartwell Estates</div>

  <div class="agent agent--broker">
    <div class="agent-name">Dana Pembrook</div>
    <div class="agent-title">Broker</div>
    <div class="agent-phone">(555).317.6624</div>
  </div>

  <div class="divider"></div>

  <div class="agent agent--realtor">
    <div class="agent-name">Marla Pembrook</div>
    <div class="agent-title">Realtor</div>
    <div class="agent-phone">(555).609.1385</div>
  </div>

  <div class="office">
    <div>418B W. Calloway Ave.</div>
    <div>Fernvale, KS. 70913</div>
    <ul class="office-list">
      <li>
        <svg viewBox="0 0 12 12"><path d="M2.5 1 L4.5 1 L5.2 3.5 L4 4.6 Q5.3 7 7.4 8 L8.5 6.8 L11 7.5 L11 9.5 Q10 11 8.5 11 Q2 9.5 1 3.5 Q1 2 2.5 1 Z" fill="var(--ink-soft)"/></svg>
        (555).240.3918
      </li>
      <li>
        <svg viewBox="0 0 12 12"><rect x="1" y="2.5" width="10" height="7" fill="none" stroke="var(--ink-soft)" stroke-width="1.3"/><path d="M1 2.5 L6 6.5 L11 2.5" fill="none" stroke="var(--ink-soft)" stroke-width="1.3"/></svg>
        pembrook@hartwellestates-demo.com
      </li>
      <li class="web">
        <svg viewBox="0 0 12 12"><circle cx="6" cy="6" r="5" fill="var(--ink-soft)"/><path d="M1 6 H11 M6 1 Q3 6 6 11 Q9 6 6 1" fill="none" stroke="var(--white)" stroke-width="0.8"/></svg>
        <span>www.<strong>hartwellestates-demo</strong>.com</span>
      </li>
    </ul>
  </div>
</section>

</body>
</html>
```